Pitch Deck Powerpoint Template for Entrepreneurship/Education Based Nonprofit

I need a stylish powerpoint design for a start-up nonprofit called Harbor Venture Works (HVW). I am building HVWs pitch deck to raise money. HVW is an entrepreneurial incubator and accelerator that seeks to identify, validate, test, and launch innovative ventures that improve public education. An example of our model, and one of our partners, is Kestrel Schools in New Orleans and New York :http://kestrelsch.example.org

We need the deck to look sleek and innovative - like a start-up pitch deck. Lots of different templates and fonts that pop off the page.

Target Market(s)

Individuals, foundations, and any other stakeholder - we are pitching a new business model and asking for money.

Industry/Entity Type

Building

Font styles to use
Sans Serif

Requirements
Must have
• A sleek/modern feel with several different template slides. charts and graphs/ strong fonts that pop off the page, use of the logo:
• It would be great to have a slide describing the 3 primary programs at Harbor Venture Works (HVW):
• - HVWspark - come in with an idea for an innovation in education, and we will do a two day workshop to examine your business assumptions and discuss next steps.
• - HVWpropell - take your idea to a prototype and launch to customers - we help you with an intensive 30 day program
• - HVWnurture - for existing nonprofit projects, we allow you to work under our umbrella to launch and build capacity
• Slides: Problem Definition, Solution, Value Proposition, Data/MEasurement, Key Partners, About the founder, Key Advisors

```html
<!DOCTYPE html>
<html lang="en">
<head>
<meta charset="utf-8">
<title>Data Measurement Concept 1</title>
<link rel="stylesheet" href="https://fonts.googleapis.com/css2?family=Oswald:wght@500&family=Open+Sans:wght@400;600;700&display=swap">
<style>
  :root {
    --stage: #000000;
    --paper: #ffffff;
    --navy: #00467f;
    --magenta: #a8218e;
    --ink: #111111;
    --axis: #333333;
    --muted: #555555;
    --green: #5a8f0a;   --green-dark: #426307;
    --orange: #f25a27;  --orange-dark: #bd330a;
    --blue: #22a7f5;    --blue-dark: #168ccc;
    --pink: #f62a7f;    --pink-dark: #a80e56;
    --teal: #19b1c3;    --teal-dark: #108f96;
    --purple: #6a14e0;  --purple-dark: #4c14a6;
    --page-no: #0b4f8c;
  }
  html, body {
    margin: 0;
    padding: 0;
    width: 1200px;
    height: 1100px;
    overflow: hidden;
    background: var(--stage);
  }
  .canvas {
    position: relative;
    width: 1200px;
    height: 1100px;
    font-family: "Open Sans", Arial, sans-serif;
  }
  .board-title {
    position: absolute;
    top: 95px;
    left: 0;
    width: 1200px;
    margin: 0;
    text-align: center;
    color: #fff;
    font-weight: 600;
    font-size: 33px;
  }
  .slide {
    position: absolute;
    left: 88px;
    top: 166px;
    width: 1024px;
    height: 768px;
    background: var(--paper);
    overflow: hidden;
  }
  .slide svg { display: block; }
  .header-band text {
    font-family: "Oswald", "Arial Narrow", sans-serif;
    font-weight: 500;
    font-size: 44px;
    fill: #fff;
  }
  .brand-name {
    font-family: "Open Sans", Arial, sans-serif;
    font-weight: 700;
    font-size: 31px;
    fill: var(--navy);
  }
  .intro {
    position: absolute;
    left: 40px;
    top: 174px;
    width: 686px;
    margin: 0;
    font-size: 16.2px;
    line-height: 27px;
    color: var(--ink);
    text-align: justify;
  }
  .axis-label { font-size: 12.5px; fill: var(--muted); }
  .category-label { font-size: 12.5px; fill: #444; }
  .share-value { font-size: 19px; font-weight: 600; fill: #fff; }
  .footer-text { font-size: 23px; font-weight: 700; fill: #fff; }
  .page-number {
    position: absolute;
    right: 22px;
    top: 1043px;
    margin: 0;
    font-size: 33px;
    color: var(--page-no);
  }
</style>
</head>
<body>
<div class="canvas">
  <h1 class="board-title">Data Measurement Concept 1</h1>

  <div class="slide">
    <svg width="1024" height="768" viewBox="88 166 1024 768" xmlns="http://www.w3.org/2000/svg">
      <defs>
        <pattern id="wave-edge" x="88" y="840" width="30" height="24" patternUnits="userSpaceOnUse">
          <path d="M0 16 Q7.5 6 15 14 T30 16 V24 H0 Z" fill="var(--magenta)"/>
          <path d="M0 16 Q7.5 6 15 14 T30 16" fill="none" stroke="var(--navy)" stroke-width="3"/>
        </pattern>
      </defs>

      <!-- header band -->
      <g class="header-band">
        <rect x="88" y="209" width="733" height="93" fill="var(--navy)"/>
        <text x="130" y="277">DATA/MEASUREMENT</text>
      </g>

      <!-- brand name -->
      <g class="brand">
        <text class="brand-name" x="848" y="238">Harbor</text>
        <text class="brand-name" x="848" y="270">Venture</text>
        <text class="brand-name" x="848" y="302">Works</text>
      </g>

      <!-- bar chart -->
      <g class="bar-chart">
        <g stroke="var(--axis)" stroke-width="1" stroke-dasharray="4 3">
          <line x1="140" y1="510" x2="810" y2="510"/>
          <line x1="140" y1="555" x2="810" y2="555"/>
          <line x1="140" y1="600" x2="810" y2="600"/>
          <line x1="140" y1="645" x2="810" y2="645"/>
          <line x1="140" y1="690" x2="810" y2="690"/>
          <line x1="140" y1="735" x2="810" y2="735"/>
        </g>
        <line x1="135" y1="474" x2="135" y2="780" stroke="var(--axis)"/>
        <line x1="135" y1="780" x2="810" y2="780" stroke="var(--axis)"/>

        <g class="axis-label" text-anchor="end">
          <text x="130" y="511">60</text>
          <text x="130" y="556">50</text>
          <text x="130" y="601">40</text>
          <text x="130" y="646">30</text>
          <text x="130" y="691">20</text>
          <text x="130" y="736">10</text>
          <text x="127" y="783">0</text>
        </g>

        <rect x="187" y="501" width="52" height="108" fill="var(--green-dark)"/>
        <rect x="187" y="609" width="52" height="171" fill="var(--green)"/>
        <rect x="293" y="550" width="52" height="111" fill="var(--orange-dark)"/>
        <rect x="293" y="661" width="52" height="119" fill="var(--orange)"/>
        <rect x="403" y="475" width="52" height="147" fill="var(--blue-dark)"/>
        <rect x="403" y="622" width="52" height="158" fill="var(--blue)"/>
        <rect x="521" y="519" width="52" height="126" fill="var(--pink-dark)"/>
        <rect x="521" y="645" width="52" height="135" fill="var(--pink)"/>
        <rect x="636" y="519" width="52" height="126" fill="var(--teal-dark)"/>
        <rect x="636" y="645" width="52" height="135" fill="var(--teal)"/>
        <rect x="750" y="625" width="52" height="75" fill="var(--purple-dark)"/>
        <rect x="750" y="700" width="52" height="80" fill="var(--purple)"/>

        <g class="category-label" text-anchor="middle">
          <text x="208" y="812">CATEGORY 1</text>
          <text x="319" y="812">CATEGORY 2</text>
          <text x="429" y="812">CATEGORY 3</text>
          <text x="547" y="812">CATEGORY 4</text>
          <text x="662" y="812">CATEGORY 5</text>
        </g>
      </g>

      <!-- share bubbles -->
      <g class="share-chain">
        <line x1="916" y1="382" x2="1050" y2="436" stroke="var(--green)"/>
        <line x1="1050" y1="436" x2="940" y2="518" stroke="var(--blue)"/>
        <line x1="940" y1="518" x2="1037" y2="621" stroke="var(--pink)"/>
        <line x1="1037" y1="621" x2="916" y2="677" stroke="var(--teal)"/>
        <line x1="916" y1="677" x2="1007" y2="783" stroke="var(--purple)"/>

        <circle cx="916" cy="382" r="37" fill="var(--green)"/>
        <circle cx="1050" cy="436" r="37" fill="var(--orange)"/>
        <circle cx="940" cy="518" r="37" fill="var(--blue)"/>
        <circle cx="1037" cy="621" r="37" fill="var(--pink)"/>
        <circle cx="916" cy="677" r="37" fill="var(--teal)"/>
        <circle cx="1007" cy="783" r="37" fill="var(--purple)"/>

        <g class="share-value" text-anchor="middle">
          <text x="916" y="389">20%</text>
          <text x="1050" y="443">10%</text>
          <text x="940" y="525">15%</text>
          <text x="1037" y="628">15%</text>
          <text x="916" y="684">30%</text>
          <text x="1007" y="790">10%</text>
        </g>
      </g>

      <!-- footer -->
      <g class="footer">
        <rect x="88" y="840" width="1024" height="24" fill="url(#wave-edge)"/>
        <rect x="88" y="862" width="1024" height="72" fill="var(--magenta)"/>
        <text class="footer-text" x="133" y="905">Page 1</text>
        <text class="footer-text" x="1058" y="905" text-anchor="end">www.hvw.example.org</text>
      </g>
    </svg>

    <p class="intro">Lorem ipsum dolor sit amet, consectetuer adipiscing elit, sed diam nonummy nibh euismod tincidunt ut laoreet dolore magna aliquam erat volutpat. Ut wisi enim ad minim veniam, quis nostrud exerci tation ullamcorper suscipit loborti.</p>
  </div>

  <p class="page-number">24</p>
</div>
</body>
</html>
```